Redesign website bus travel company Falk Brenz

We require a complete redesign of the website of Reisebüro Falk Brenz, an established bus tour operator based in Graubünden (www.falkbrenz.ch). For years, the company has specialized in multi-day tours throughout Europe, as well as day trips such as shopping trips to Innsbruck or Como, music tours, and market visits, primarily for seniors, as well as car rentals for clubs and companies.

The new website requires a video header with overlay text, red as the primary corporate color, complemented by black and gray, and a highly simplified navigation with two main sections: "Our Trips" and "Bus Rental." The remaining sections must be accessible via the "Menu" menu item. The design should be user-friendly for all age groups and mobile-responsive.

The goal is a trustworthy, modern website that reflects personal service and many years of experience.
The new logo can be found in the files, as well as a few pictures.

Target Market(s)

Guests of bus tours (day and multi-day trips) and bus rentals (clubs, companies, etc.)

Industry/Entity Type

Busreisen und Busvermietung

Number of Pages Required

1 page

Requirements
Must have
• Red as primary color, video header, simple UX for target group seniors
Nice to have
• Photo galleries of destinations and the vehicle fleet

```html
<!DOCTYPE html>
<html lang="en">
<head>
<meta charset="utf-8">
<title>Falk Brenz – Bus Travel</title>
<link rel="stylesheet" href="https://fonts.googleapis.com/css2?family=Anton&family=Roboto:wght@400;500;700&display=swap">
<style>
:root{
  --red:#b5000f;
  --red-dark:#8c000b;
  --black:#111;
  --dark:#1c1c1e;
  --gray:#f1f1f1;
  --ring:#ececec;
  --text:#555;
  --white:#fff;
}
*{margin:0;padding:0;box-sizing:border-box}
html,body{width:1200px;height:4121px;overflow:hidden}
body{position:relative;background:var(--white);font-family:'Roboto',sans-serif;color:var(--black)}
.abs{position:absolute}
.heading{font-family:'Anton',sans-serif;font-weight:400;color:var(--black);letter-spacing:.2px}
.btn{position:absolute;display:flex;align-items:center;justify-content:center;background:var(--red);color:#fff;font:700 13px 'Roboto',sans-serif;text-transform:uppercase;border-radius:24px;letter-spacing:.3px}

/* nav */
.topbar{left:0;top:0;width:1200px;height:80px;background:var(--red)}
.brand{left:145px;top:22px;font:700 28px/36px 'Roboto',sans-serif;color:#fff;display:flex;align-items:center;gap:10px}
.brand i{width:14px;height:14px;border-radius:50%;background:#fff;display:block}
.nav{right:140px;top:0;display:flex;height:80px}
.nav a{color:#fff;font:500 15px 'Roboto',sans-serif;text-decoration:none;display:flex;align-items:center;gap:8px;padding:0 22px}
.nav a.active{background:#1a0a0a}
.nav .burger{display:flex;flex-direction:column;gap:3px}
.nav .burger i{display:block;width:16px;height:2px;background:#fff}

/* hero */
.hero{left:0;top:80px;width:1200px;height:720px;overflow:hidden}
.hero-photo{position:absolute;inset:0;background:linear-gradient(180deg,#3d7ed8 0%,#8fbcef 22%,#d8e04a 40%,#e9d720 55%,#7fb02c 75%,#3c8a1d 100%)}
.hero-wave{position:absolute;left:0;top:0}
.play{left:803px;width:62px;height:62px;border-radius:50%;background:#e4b819;display:flex;align-items:center;justify-content:center}
.play span{width:40px;height:40px;border-radius:50%;background:var(--red);display:flex;align-items:center;justify-content:center}
.hero-badge{left:652px;top:418px;width:382px;height:382px;border-radius:50%;background:rgba(240,240,225,.85);display:flex;align-items:center;justify-content:center}
.hero-badge .inner{width:304px;height:304px;border-radius:50%;background:#fff;box-shadow:0 4px 14px rgba(0,0,0,.12);text-align:center;padding-top:56px}
.hero-badge h1{font-family:'Anton',sans-serif;font-weight:400;color:var(--red);font-size:42px;line-height:46px}
.hero-badge h2{font-family:'Anton',sans-serif;font-weight:400;font-size:34px;line-height:40px}
.hero-badge p{font-size:11px;line-height:13px;color:#444;width:200px;margin:8px auto 0}

/* services */
.section-title{width:1200px;text-align:center;font-size:48px;line-height:54px}
.service{width:200px;text-align:center}
.service .icon{width:124px;height:124px;border-radius:50%;background:#f6d6d8;margin:0 auto;display:flex;align-items:center;justify-content:center}
.service .icon span{width:108px;height:108px;border-radius:50%;background:var(--red);display:flex;align-items:center;justify-content:center}
.service p{font:500 19px 'Roboto',sans-serif;margin-top:24px}
.arrow{width:38px;height:38px;border-radius:50%;background:#eee;display:flex;align-items:center;justify-content:center}

/* round photo */
.round{border-radius:50%;background:var(--ring);display:flex;align-items:center;justify-content:center}
.round .photo{border-radius:50%;border:3px solid var(--red)}
.dot{width:22px;height:22px;border-radius:50%;background:var(--red)}

.about p.body{font-size:14px;line-height:22.4px;color:var(--text);width:410px}

/* bus rental */
.rental{left:0;top:1800px;width:1200px;height:505px;background:linear-gradient(100deg,#2b2b2e 0%,#4a4642 45%,#3b3a3a 65%,#121416 100%);overflow:hidden}

/* trips */
.trip{position:absolute;width:301px;height:230px;border-radius:8px;overflow:hidden}
.trip-card{background:var(--gray);text-align:center;padding:24px 0 0}
.trip-card h3{font:500 20px 'Roboto',sans-serif;margin-bottom:10px}
.trip-card p{font-size:12.5px;line-height:20px;color:#666;width:250px;margin:0 auto}
.trip-card .btn{position:relative;width:152px;height:44px;margin:14px auto 0}

/* accessibility */
.info{font-size:19px;line-height:28px}
.info .lbl{color:#555}
.info b{font-weight:700;color:var(--black)}

/* footer */
.footer{left:0;top:3520px;width:1200px;height:601px;background:linear-gradient(180deg,#3a0a0c 0%,#1b0607 40%,#0d0d0e 100%);overflow:hidden}
.f-title{color:#fff;font:500 20px/28px 'Roboto',sans-serif;text-transform:uppercase}
.f-link{color:#fff;font-size:14px;line-height:32px;display:flex;align-items:center;gap:14px}
.f-link::before{content:"›";color:var(--red);font-weight:700}
.c-item{display:flex;gap:12px;color:#fff}
.c-item .ic{width:42px;height:42px;border-radius:50%;background:var(--red);flex:none;display:flex;align-items:center;justify-content:center}
.c-item b{font-size:14px;display:block}
.c-item small{font-size:11px;line-height:14px;display:block}
</style>
</head>
<body>

<!-- navigation -->
<header class="abs topbar">
  <div class="abs brand"><i></i>Falk Brenz</div>
  <nav class="abs nav">
    <a class="active">Our Trips</a>
    <a>Bus Rental</a>
    <a><span class="burger"><i></i><i></i><i></i></span>Menu</a>
  </nav>
</header>

<!-- hero -->
<section class="abs hero">
  <div class="hero-photo" role="img" aria-label="Touring coach parked on green grass beside a yellow rapeseed field under blue sky"></div>
  <svg class="hero-wave" width="1200" height="720" viewBox="0 0 1200 720">
    <path d="M0 600 C120 690 260 720 360 705 C560 680 760 560 900 520 C1010 490 1120 540 1200 600 L1200 720 L0 720 Z" fill="#fff"/>
    <path d="M0 600 C120 690 260 720 360 705 C560 680 760 560 900 520 C1010 490 1120 540 1200 600 L1200 560 C1120 500 1010 470 900 500 C760 540 560 650 360 670 C250 680 120 660 0 570 Z" fill="var(--red)"/>
  </svg>
  <div class="abs play" style="top:200px"><span><svg width="14" height="16"><path d="M2 1 L13 8 L2 15 Z" fill="#fff"/></svg></span></div>
</section>
<div class="abs hero-badge">
  <div class="inner">
    <h1>THE 2025</h1>
    <h2>Travel<br>Program is Here!</h2>
    <p>You can find all tours and day trips online under the "Day Trips" and "Holiday Trips" sections - browse through them, there's something for everyone.</p>
  </div>
</div>

<!-- services -->
<h2 class="abs heading section-title" style="left:0;top:872px">We Are Happy To<br>Recommend Ourselves For</h2>
<div class="abs arrow" style="left:53px;top:1091px"><svg width="16" height="12"><path d="M15 6H2M6 1 1 6l5 5" stroke="#111" stroke-width="1.8" fill="none"/></svg></div>
<div class="abs arrow" style="left:1109px;top:1091px"><svg width="16" height="12"><path d="M1 6h13M10 1l5 5-5 5" stroke="#111" stroke-width="1.8" fill="none"/></svg></div>
<div class="abs service" style="left:157px;top:1016px">
  <div class="icon"><span><svg width="52" height="40" viewBox="0 0 52 40"><path d="M8 20 L14 10 H38 L44 20 H48 V32 H4 V20 Z" fill="#fff"/><circle cx="14" cy="33" r="5" fill="var(--red)" stroke="#fff" stroke-width="3"/><circle cx="38" cy="33" r="5" fill="var(--red)" stroke="#fff" stroke-width="3"/><rect x="16" y="2" width="20" height="7" fill="#fff"/></svg></span></div>
  <p>Car Travel</p>
</div>
<div class="abs service" style="left:385px;top:1016px">
  <div class="icon"><span><svg width="44" height="48" viewBox="0 0 44 48"><path d="M22 40 C4 26 4 8 15 8 C19 8 21 11 22 13 C23 11 25 8 29 8 C40 8 40 26 22 40 Z" fill="none" stroke="#fff" stroke-width="3.5"/><path d="M22 28 C14 21 15 16 18 16 C20 16 21 18 22 19 C23 18 24 16 26 16 C29 16 30 21 22 28 Z" fill="#fff"/></svg></span></div>
  <p>Day Trips</p>
</div>
<div class="abs service" style="left:613px;top:1016px">
  <div class="icon"><span><svg width="48" height="48" viewBox="0 0 48 48"><rect x="14" y="18" width="20" height="20" fill="#fff"/><rect x="10" y="38" width="28" height="5" fill="#fff"/><path d="M8 6 L18 16 M40 6 L30 16" stroke="#fff" stroke-width="4"/><circle cx="24" cy="10" r="4" fill="#fff"/></svg></span></div>
  <p>Music Tours</p>
</div>
<div class="abs service" style="left:841px;top:1016px">
  <div class="icon"><span><svg width="46" height="44" viewBox="0 0 46 44"><rect x="3" y="10" width="40" height="30" rx="5" fill="#fff"/><rect x="15" y="3" width="16" height="9" rx="2" fill="none" stroke="#fff" stroke-width="3"/><circle cx="23" cy="25" r="7" fill="var(--red)"/></svg></span></div>
  <p>Holiday Trips</p>
</div>

<!-- about -->
<div class="abs round" style="left:167px;top:1297px;width:410px;height:410px">
  <div class="photo" role="img" aria-label="Coach parked on a lawn under pine trees and blue sky" style="width:364px;height:364px;background:linear-gradient(180deg,#3f7fd0 0%,#a9c9ee 45%,#4e7b3a 62%,#7da058 100%)"></div>
</div>
<div class="abs dot" style="left:218px;top:1381px"></div>
<section class="about">
  <h2 class="abs heading" style="left:628px;top:1300px;font-size:50px;line-height:60px">About Us</h2>
  <p class="abs" style="left:629px;top:1372px;color:var(--red);font:700 19px 'Roboto',sans-serif">Experience the world with us</p>
  <p class="abs body" style="left:629px;top:1412px">The Brenz travel agency has existed for over 60 years and has been run by Marco Valär and Luca Tschudi, the fourth generation of the family, since August 1, 2013. Our travel industry expertise, friendly and reliable service, and competitive prices set us apart from the competition. Nina Caduff, Selina Buchli, our office staff, will be happy to assist you with travel arrangements. Dario Casutt, Jonas Meier, and Marco Valär, along with other reliable and friendly chauffeurs, will ensure that you reach your destination safely and comfortably.</p>
  <div class="btn" style="left:632px;top:1651px;width:152px;height:45px">Learn More</div>
</section>

<!-- bus rental -->
<section class="abs rental">
  <div class="abs" role="img" aria-label="Tour guide speaking into a microphone inside a coach" style="inset:0;background:radial-gradient(ellipse at 62% 55%,rgba(160,140,120,.55),transparent 55%)"></div>
  <div class="abs" style="inset:0;background:linear-gradient(90deg,rgba(0,0,0,.35),rgba(0,0,0,0) 50%)"></div>
  <svg class="abs" style="left:0;top:0" width="1200" height="505" viewBox="0 0 1200 505">
    <path d="M0 0 H1200 V95 C1120 120 1040 175 980 190 C900 115 560 -10 340 25 C200 45 80 80 0 105 Z" fill="#fff"/>
  </svg>
  <h2 class="abs heading" style="left:143px;top:200px;font-size:48px;line-height:56px;color:#fff">Bus Rental</h2>
  <p class="abs heading" style="left:143px;top:270px;font-size:24px;line-height:30px;color:#fff">13 + 1 seater Vanta Cruiser 316</p>
  <div class="btn" style="left:143px;top:314px;width:206px;height:45px">View More Details</div>
</section>
<div class="abs round" style="left:653px;top:1780px;width:350px;height:350px">
  <div class="photo" role="img" aria-label="Silver minibus parked in front of mountains" style="width:284px;height:284px;background:linear-gradient(180deg,#6f9bd2 0%,#b9c6cf 40%,#a3a6a8 65%,#5f6a52 100%)"></div>
</div>

<!-- trips -->
<h2 class="abs heading section-title" style="left:0;top:2396px;font-size:50px">Our Trips</h2>
<div class="trip" role="img" aria-label="Hikers walking across a hill at sunset" style="left:144px;top:2497px;background:linear-gradient(180deg,#4f6c88 0%,#d9a65a 55%,#3a2a18 100%)"></div>
<div class="trip trip-card" style="left:450px;top:2497px">
  <h3>Holiday Trips</h3>
  <p>Coach ride, 3 nights/breakfast at the modern Hotel Centrale Kirchberg, 2 dinners at the hotel, guided tour of a sparkling wine cellar</p>
  <div class="btn">Learn More</div>
</div>
<div class="trip" role="img" aria-label="Group of travellers waving among tea fields and mountains" style="left:755px;top:2497px;background:linear-gradient(180deg,#9fb4b8 0%,#6f8c63 45%,#4d7a2e 100%)"></div>
<div class="trip trip-card" style="left:144px;top:2727px">
  <h3>Day Trips</h3>
  <p>Coach ride, 3 nights/breakfast at the modern Hotel Centrale Kirchberg, 2 dinners at the hotel, guided tour of a sparkling wine cellar</p>
  <div class="btn">Learn More</div>
</div>
<div class="trip" role="img" aria-label="Old town with a stone bridge over a river" style="left:450px;top:2727px;background:linear-gradient(180deg,#7ea6d4 0%,#b79a74 40%,#6d7a4a 75%,#3e5c2e 100%)"></div>
<div class="trip trip-card" style="left:755px;top:2727px">
  <h3>Group Tours</h3>
  <p>Are you looking for a chauffeur-driven coach that will pick you up from your doorstep and drop you off again – all at a fair price?</p>
  <div class="btn">Learn More</div>
</div>

<!-- accessibility -->
<div class="abs round" style="left:167px;top:3073px;width:410px;height:410px">
  <div class="photo" role="img" aria-label="Smiling staff member in uniform with neck scarf" style="width:364px;height:364px;background:linear-gradient(135deg,#5b7fa6 0%,#d8c3a8 45%,#e8e2da 70%,#8ea2b8 100%)"></div>
</div>
<div class="abs dot" style="left:218px;top:3157px"></div>
<section>
  <h2 class="abs heading" style="left:628px;top:3075px;font-size:50px;line-height:60px">Accessibility</h2>
  <p class="abs" style="left:629px;top:3147px;font-size:19px;line-height:28px;width:430px;color:#222">We would be happy to advise you personally at the following times:</p>
  <svg class="abs" style="left:631px;top:3232px" width="18" height="18"><circle cx="9" cy="9" r="7" fill="none" stroke="var(--red)" stroke-width="2"/><path d="M9 5v4l3 2" stroke="var(--red)" stroke-width="2" fill="none"/></svg>
  <div class="abs info" style="left:666px;top:3225px"><span class="lbl">Monday - Friday</span><br><b>8:00 a.m. - 12:00 p.m.<br>1:30 p.m. - 5:00 p.m.</b></div>
  <svg class="abs" style="left:631px;top:3337px" width="18" height="18"><path d="M4 1 L7 5 L5 7 C6 10 8 12 11 13 L13 11 L17 14 L15 17 C8 17 1 10 1 3 Z" fill="var(--red)"/></svg>
  <div class="abs info" style="left:666px;top:3330px"><span class="lbl">Phone:</span><br><b>081 555 41 20</b></div>
  <svg class="abs" style="left:631px;top:3420px" width="20" height="14"><rect x="0" y="0" width="20" height="14" rx="2" fill="var(--red)"/><path d="M1 1 L10 8 L19 1" stroke="#fff" stroke-width="1.5" fill="none"/></svg>
  <div class="abs info" style="left:666px;top:3410px"><span class="lbl">Email:</span><br><b>info@falkbrenz.ch</b></div>
</section>

<!-- footer -->
<footer class="abs footer">
  <svg class="abs" style="left:0;top:0" width="1200" height="140" viewBox="0 0 1200 140">
    <path d="M0 0 H1200 V120 C1000 40 700 20 500 50 C300 80 150 60 0 30 Z" fill="#fff"/>
    <path d="M0 30 C150 60 300 80 500 50 C700 20 1000 40 1200 120 V140 C1000 70 700 50 500 85 C300 115 150 100 0 70 Z" fill="var(--red)"/>
  </svg>
  <div class="abs" style="left:143px;top:160px;font:700 64px/74px 'Roboto',sans-serif;color:var(--red)">Falk Brenz</div>
  <div class="abs" style="left:143px;top:234px;width:395px;height:2px;background:var(--red)"></div>

  <p class="abs f-title" style="left:143px;top:285px">Subscribe to<br>our newsletter</p>
  <div class="abs" style="left:143px;top:348px;width:271px;height:40px;background:#fff;display:flex;align-items:center;justify-content:space-between;padding:0 14px;font-size:11px;color:#444">Email address<svg width="14" height="14"><path d="M1 7 L13 1 L9 13 L7 8 Z" fill="var(--red)"/></svg></div>
  <div class="abs" style="left:143px;top:405px;display:flex;gap:8px">
    <span style="width:27px;height:27px;border-radius:50%;background:#fff"></span>
    <span style="width:27px;height:27px;border-radius:50%;background:var(--red)"></span>
    <span style="width:27px;height:27px;border-radius:50%;background:#fff"></span>
  </div>

  <p class="abs f-title" style="left:495px;top:285px">Contact Info</p>
  <div class="abs c-item" style="left:485px;top:325px"><span class="ic"><svg width="14" height="18"><path d="M7 17 C2 10 1 8 1 6 A6 6 0 0 1 13 6 C13 8 12 10 7 17Z" fill="#fff"/><circle cx="7" cy="6" r="2.2" fill="var(--red)"/></svg></span><div><b>Address</b><small>Talweg 9, 7012 Felsberg,<br>Switzerland</small></div></div>
  <div class="abs c-item" style="left:485px;top:385px"><span class="ic"><svg width="18" height="13"><rect width="18" height="13" rx="2" fill="#fff"/><path d="M1 1 L9 7 L17 1" stroke="var(--red)" stroke-width="1.5" fill="none"/></svg></span><div><b>Email</b><small style="margin-top:6px">info@falkbrenz.ch</small></div></div>
  <div class="abs c-item" style="left:485px;top:440px"><span class="ic"><svg width="16" height="16"><path d="M3 1 L6 5 L4 7 C5 9 7 11 9 12 L11 10 L15 13 L13 15 C7 15 1 9 1 3 Z" fill="#fff"/></svg></span><div><b>Phone</b><small style="margin-top:6px">+41(0)81 555 41 20</small></div></div>

  <p class="abs f-title" style="left:765px;top:285px">Quick Links</p>
  <div class="abs" style="left:765px;top:326px">
    <div class="f-link">Home</div><div class="f-link">About</div><div class="f-link">Services</div><div class="f-link">Contact</div>
  </div>
  <div class="abs" style="left:900px;top:326px">
    <div class="f-link">Terms and Condition</div><div class="f-link">Privacy policy</div><div class="f-link">Help</div><div class="f-link">Support</div>
  </div>

  <p class="abs" style="left:0;top:552px;width:1200px;text-align:center;color:#fff;font-size:13px">© Copyrights 2025 | All Rights Reserved</p>
</footer>

</body>
</html>
```